Young, dynamic furniture company needs a new business card design

We require a new business card design for our modern furniture company which supplies furniture and appliances to the property and development market.
Oakridge Interiors has become one of the leading furniture & appliance suppliers to the property market withing London. With over 10 years experience, we have increased our business to supply not only private landlords and managing agents, but also property developers, housing associations and local councils.
We offer not only a complete range of furniture which includes beds, wardrobes, dining sets and sofas, but also a high quality, full delivery and assembly service to help you with all our furnishing needs.

Target Market(s)

Private landlords, estate agents, letting agents, property management companies

Industry/Entity Type

Business

Contact Information for Business Card

Name,
Title,
Address,
Mobile,
Telephone,
Fax, Website, email address

Font styles to use
Sans Serif

Colors
3176b5
0555a3
85abd2
cfdeed

Requirements
Must have
• All the above information for each of our staff, along with our logo

```html
<!DOCTYPE html>
<html lang="en">
<head>
<meta charset="utf-8">
<title>Oakridge Interiors – Business Card</title>
<link rel="stylesheet" href="https://fonts.googleapis.com/css2?family=Lato:wght@300;400;700&display=swap">
<style>
  :root {
    --brand-deep: #0555a3;
    --brand-mid: #3176b5;
    --brand-soft: #85abd2;
    --brand-pale: #cfdeed;
    --ink: #1a1a1a;
    --paper: #ffffff;
    --backdrop: #e6e8eb;
  }
  * { box-sizing: border-box; margin: 0; padding: 0; }
  html, body {
    width: 1200px; height: 900px; overflow: hidden;
    background: var(--backdrop);
    font-family: "Lato", sans-serif;
  }
  .canvas {
    position: relative; width: 1200px; height: 900px;
  }
  .card {
    position: absolute; left: 280px; width: 640px; height: 366px;
    overflow: hidden;
    box-shadow: 0 6px 18px rgba(0,0,0,0.18);
  }
  .card--back { top: 60px; background: var(--brand-deep); color: var(--paper); }
  .card--front { top: 474px; background: var(--paper); }

  .brand {
    position: absolute; display: flex; flex-direction: column; align-items: center;
    color: var(--paper);
  }
  .brand__mark {
    width: 58px; height: 58px; border: 3px solid var(--paper); margin-bottom: 26px;
  }
  .brand__name {
    font-weight: 300; font-size: 34px; letter-spacing: 0.5px; text-transform: uppercase;
    white-space: nowrap;
  }
  .brand__tagline {
    font-weight: 300; font-size: 15px; letter-spacing: 0.6px; text-transform: uppercase;
    margin-top: 4px; white-space: nowrap;
  }
  .card--back .brand { left: 0; right: 0; top: 86px; }
  .brand__web {
    font-weight: 400; font-size: 18px; letter-spacing: 2px; margin-top: 26px;
  }

  .front__panel {
    position: absolute; left: 0; top: 0; bottom: 0; width: 296px;
    background: var(--brand-mid);
  }
  .front__rule {
    position: absolute; left: 301px; top: 0; bottom: 0; width: 2px;
    background: var(--brand-soft);
  }
  .card--front .brand { left: 0; width: 296px; top: 92px; }
  .card--front .brand__name { font-size: 26px; }
  .card--front .brand__tagline { font-size: 12px; }

  .contact {
    position: absolute; left: 344px; top: 70px; color: var(--ink);
  }
  .contact__name { font-size: 33px; font-weight: 400; line-height: 1.1; }
  .contact__title { font-size: 19px; color: var(--brand-mid); margin-top: 2px; }
  .contact__address { font-size: 19px; line-height: 1.3; margin-top: 16px; }
  .contact__list { list-style: none; margin-top: 10px; }
  .contact__item {
    display: flex; align-items: center; gap: 12px;
    font-size: 19px; line-height: 1.35;
  }
  .contact__icon { width: 16px; height: 16px; flex: none; fill: var(--brand-mid); }
</style>
</head>
<body>
<main class="canvas">
  <section class="card card--back" aria-label="Card back">
    <div class="brand">
      <span class="brand__mark"></span>
      <span class="brand__name">Oakridge Interiors</span>
      <span class="brand__tagline">Trade Furniture Solutions</span>
      <span class="brand__web">www.trade.oakridge.co.uk</span>
    </div>
  </section>

  <section class="card card--front" aria-label="Card front">
    <div class="front__panel">
      <div class="brand">
        <span class="brand__mark"></span>
        <span class="brand__name">Oakridge Interiors</span>
        <span class="brand__tagline">Trade Furniture Solutions</span>
      </div>
    </div>
    <div class="front__rule"></div>

    <div class="contact">
      <p class="contact__name">Daniel Hartley</p>
      <p class="contact__title">Manager</p>
      <p class="contact__address">27B Elmfield Trading Estate<br>Northwood Green, London</p>
      <ul class="contact__list">
        <li class="contact__item">
          <svg class="contact__icon" viewBox="0 0 16 16"><path d="M3.2 1l2.6 3.2-1.4 1.6c.9 2 2.4 3.5 4.4 4.4l1.6-1.4L13.6 11.4l-1.5 2.8C6.5 14 2 9.5 1.8 3.9z"/></svg>
          <span>020 7946 0321</span>
        </li>
        <li class="contact__item">
          <svg class="contact__icon" viewBox="0 0 16 16"><path d="M4 1h8v14H4zM5.5 2.5v8.5h5V2.5zM7 12.5h2v1H7z" fill-rule="evenodd"/></svg>
          <span>020 7946 0500</span>
        </li>
        <li class="contact__item">
          <svg class="contact__icon" viewBox="0 0 16 16"><path d="M1 3h14v10H1zM2 4l6 5 6-5"/><path d="M2 4l6 5 6-5" fill="none" stroke="#fff" stroke-width="1.2"/></svg>
          <span>info@trade.oakridge.co.uk</span>
        </li>
        <li class="contact__item">
          <svg class="contact__icon" viewBox="0 0 16 16"><circle cx="8" cy="8" r="7"/><g fill="none" stroke="#fff" stroke-width="1"><ellipse cx="8" cy="8" rx="3" ry="7"/><path d="M1 8h14M2.5 4.5h11M2.5 11.5h11"/></g></svg>
          <span>www.trade.oakridge.co.uk</span>
        </li>
      </ul>
    </div>
  </section>
</main>
</body>
</html>
```